Clinic for cellulit and fat removal

Name of clinic :
Lirava
- Body & Health (this has to be written on the site.)
I need CMS for me to be able to make changes myself.
A webpage for woman searching for a solution to remove fat and cellulit.
The owner is a brazilian woman in Denmark, and want her sense of aestetic shines thru the website.
There needs to be a slide show on the landing page showing big sliding pictures, of the clinic and and the treatments.
The Cryolipolysis, is a treatment freezing fat and cellulit, and this treatment will be the Attraction of the clinic.
Needs These pages in a horisontal fasion. (written in Danish)
Lirava
Behandlinger
- Cryolipolysis
- Trimflox
- Lymfemassage
- Korathelix
- Amberline Tide
Produkter
Priser
Kontakt
Clinic
Coded - Design and coding required
5+ page

```html
<!DOCTYPE html>
<html lang="da">
<head>
<meta charset="utf-8">
<title>Lirava – Body &amp; Health – Cryolipolysis</title>
<link href="https://fonts.googleapis.com/css2?family=Open+Sans:wght@300;400;600&display=swap" rel="stylesheet">
<style>
:root{
  --teal:#8dd0b7;
  --teal-dark:#6fbf9f;
  --ink:#2b2b2b;
  --text:#555;
  --nav:#2e2e2e;
  --nav-line:#1f1f1f;
  --pink:#c98bb4;
  --footer:#f4f4f4;
  --white:#fff;
  --border:#dcdcdc;
}
*{box-sizing:border-box;margin:0;padding:0}
html,body{width:822px;height:1200px;overflow:hidden;background:var(--white)}
body{position:relative;font-family:"Open Sans",Arial,sans-serif;color:var(--text)}
.abs{position:absolute}

/* header */
.brand{left:68px;top:14px;display:flex;align-items:center;gap:10px}
.brand-dot{width:14px;height:14px;border-radius:50%;background:var(--teal)}
.brand-name{font-size:34px;font-weight:300;color:var(--ink);line-height:1}
.brand-tag{left:104px;top:60px;font-size:11px;color:var(--ink);font-weight:400;letter-spacing:.5px}
.search{left:498px;top:31px;width:158px;height:24px;border:1px solid #c9c9c9;border-radius:2px;font-size:8px;color:#333;padding:0 8px;display:flex;align-items:center;justify-content:space-between}
.lang{left:680px;top:38px;font-size:10px;color:#444}
.lang .on{color:#4aa64a}

/* nav */
.nav{left:0;top:90px;width:822px;height:35px;background:var(--nav)}
.nav a{position:absolute;top:0;height:35px;line-height:35px;color:var(--white);font-size:12px;text-decoration:none;text-align:center}
.nav .active{background:var(--teal)}
.nav .sep{position:absolute;top:0;width:1px;height:35px;background:var(--nav-line)}

/* hero */
.hero{left:0;top:125px;width:822px;height:210px;overflow:hidden}
.hero-photo{width:100%;height:100%;background:linear-gradient(100deg,#d7a9c9 0%,#c889b4 45%,#cf9cc0 75%,#dcb4cf 100%)}
.hero-title{right:67px;top:56px;color:var(--white);font-size:32px;font-weight:300;letter-spacing:-.5px}
.hero svg{position:absolute;left:0;top:0}

/* intro */
.intro-photo{left:68px;top:402px;width:299px;height:243px;background:linear-gradient(135deg,#e9e4e3 0%,#c7b3bd 40%,#b59a8a 70%,#ece8e6 100%)}
.intro-text{left:394px;top:408px;width:362px}
.intro-text h1{font-size:29px;font-weight:300;color:var(--ink);letter-spacing:-.5px;margin-bottom:9px}
.intro-text p{font-size:7.5px;line-height:15.2px;color:var(--text);margin-bottom:8px}

/* before after */
.results{left:0;top:719px;width:822px;height:231px;background:var(--teal)}
.results h2{position:absolute;left:0;width:822px;top:36px;text-align:center;font-size:27px;font-weight:300;color:var(--white)}
.thumb{position:absolute;top:85px;width:163px;height:97px;border:2px solid var(--white);box-shadow:0 6px 5px -4px rgba(0,0,0,.35)}

/* footer */
.footer{left:0;top:950px;width:822px;height:212px;background:var(--footer)}
.f-brand{left:68px;top:1004px;display:flex;align-items:center;gap:8px}
.f-brand .brand-name{font-size:30px}
.f-tag{left:100px;top:1042px;font-size:10px;color:var(--ink)}
.social{left:67px;top:1072px;display:flex;gap:3px}
.social span{width:16px;height:16px;border:1px solid #888;border-radius:50%}
.f-head{font-size:15px;font-weight:300;color:var(--ink)}
.links{left:226px;top:985px}
.links ul{list-style:none;margin-top:16px}
.links li{font-size:7.5px;color:#444;height:15.3px;display:flex;align-items:center;gap:6px}
.links li::before{content:"";width:5px;height:5px;border-radius:50%;background:var(--teal)}
.news{left:368px;top:985px;width:200px}
.news p{font-size:7.5px;line-height:13px;color:#444;margin-top:23px}
.field{position:absolute;left:0;width:200px;height:29px;background:var(--white);border:1px solid #e3e3e3;font-size:7.5px;color:#555;padding:0 9px;display:flex;align-items:center}
.subscribe{position:absolute;right:0;top:0;width:67px;height:29px;background:var(--teal);color:var(--white);font-size:8px;display:flex;align-items:center;justify-content:center}
.contact{left:615px;top:985px;width:160px}
.contact .addr{margin-top:17px;font-size:8.5px;line-height:13.5px;color:#444;letter-spacing:.2px}
.contact .row{display:flex;align-items:center;gap:9px;font-size:8.5px;color:#444;margin-top:6px}
.bottom{left:0;top:1162px;width:822px;height:38px;border-top:1px solid #e0e0e0;text-align:center;font-size:7.5px;color:#444;line-height:38px}
</style>
</head>
<body>

<header>
  <div class="abs brand"><span class="brand-dot"></span><span class="brand-name">Lirava</span></div>
  <div class="abs brand-tag">Body &amp; Health</div>
  <div class="abs search"><span>SEARCH</span>
    <svg width="9" height="9" viewBox="0 0 10 10"><circle cx="4" cy="4" r="3" fill="none" stroke="#222" stroke-width="1.5"/><line x1="6.2" y1="6.2" x2="9" y2="9" stroke="#222" stroke-width="1.6"/></svg>
  </div>
  <div class="abs lang">Danish I <span class="on">English</span></div>
</header>

<nav class="abs nav">
  <a style="left:70px;width:70px">Home</a>
  <a style="left:156px;width:70px">Lirava</a>
  <a class="active" style="left:231px;width:111px">Behandlinger</a>
  <a style="left:348px;width:76px">Produkter</a>
  <span class="sep" style="left:433px"></span>
  <a style="left:436px;width:64px">Priser</a>
  <span class="sep" style="left:503px"></span>
  <a style="left:508px;width:68px">Kontakt</a>
</nav>

<section class="abs hero">
  <div class="hero-photo" role="img" aria-label="Cryolipolysis treatment in the clinic, pink toned"></div>
  <svg width="822" height="210" viewBox="0 0 822 210">
    <path d="M0,195 C120,215 260,200 420,165 C560,138 700,130 822,200 L822,210 L0,210 Z" fill="#fff"/>
    <path d="M0,195 C120,215 260,200 420,165 C560,138 700,130 822,200" fill="none" stroke="#8dd0b7" stroke-width="2.5"/>
    <path d="M358,192 C470,160 620,150 756,198 C630,162 500,168 358,192 Z" fill="#8dd0b7"/>
  </svg>
  <div class="abs hero-title">Cryolipolysis</div>
</section>

<main>
  <div class="abs intro-photo" role="img" aria-label="Woman receiving cryolipolysis treatment"></div>
  <article class="abs intro-text">
    <h1>Cryolipolysis</h1>
    <p>Sed ut perspiciatis unde omnis iste natus error sit voluptatem accusantium doloremque laudantium, totam rem aperiam, eaque ipsa quae ab illo inventore veritatis et quasi architecto beatae vitae dicta sunt explicabo. Nemo enim ipsam voluptatem quia voluptas sit aspernatur aut odit aut fugit, sed quia consequuntur magni dolores eos qui ratione voluptatem sequi nesciunt.</p>
    <p>Ut enim ad minima veniam, quis nostrum exercitationem ullam corporis suscipit laboriosam, nisi ut aliquid ex ea commodi consequatur? Quis autem vel eum iure reprehenderit qui in ea voluptate velit esse quam nihil molestiae consequatur, vel illum qui dolorem eum fugiat quo voluptas nulla pariatur?</p>
    <p>Sed ut perspiciatis unde omnis iste natus error sit voluptatem accusantium doloremque laudantium, totam rem aperiam, eaque ipsa quae ab illo inventore veritatis et quasi architecto beatae vitae dicta sunt explicabo. Nemo enim ipsam voluptatem quia voluptas sit aspernatur</p>
  </article>

  <section class="abs results">
    <h2>før efter</h2>
    <div class="thumb" style="left:68px;background:linear-gradient(90deg,#9c9a7f,#b9a4b4 50%,#a8c0c8)" role="img" aria-label="Before and after photo, bikini"></div>
    <div class="thumb" style="left:244px;background:linear-gradient(90deg,#c9c9c9,#e0dcd8 50%,#c4c4c4)" role="img" aria-label="Before and after photo, side profile"></div>
    <div class="thumb" style="left:419px;background:linear-gradient(90deg,#f0e4dc,#3a3a3a 50%,#f2e8e2)" role="img" aria-label="Before and after photo, waist"></div>
    <div class="thumb" style="left:592px;background:linear-gradient(90deg,#f6f1ed,#e6c2a8 50%,#f6f1ed)" role="img" aria-label="Before and after photo, back"></div>
  </section>
</main>

<footer>
  <div class="abs footer"></div>
  <div class="abs f-brand"><span class="brand-dot"></span><span class="brand-name">Lirava</span></div>
  <div class="abs f-tag">Body &amp; Health</div>
  <div class="abs social"><span></span><span></span><span></span><span></span><span></span></div>

  <div class="abs links">
    <div class="f-head">Quick Links</div>
    <ul><li>Home</li><li>Lirava</li><li>Behandlinger</li><li>Produkter</li><li>Priser</li><li>Blog</li><li>Kontakt</li></ul>
  </div>

  <div class="abs news">
    <div class="f-head">Sign up for Newsletter</div>
    <p>Sed ut perspiciatis unde omnis iste natus error sit voluptatem accusantium doloremque</p>
    <div class="field" style="top:73px">Enter Name</div>
    <div class="field" style="top:108px">Enter Email<span class="subscribe">SUBSCRIBE</span></div>
  </div>

  <div class="abs contact">
    <div class="f-head">Contact Us</div>
    <div class="addr">Lirava<br>12 Lindegade&nbsp; Aarhus C<br>8000</div>
    <div class="row"><svg width="12" height="12" viewBox="0 0 12 12"><path d="M2,1 L4.5,1 L5.5,4 L4,5 C4.8,6.8 5.8,7.8 7,8.5 L8,7 L11,8 L11,10.5 C6,11 1,6 1.5,2 Z" fill="none" stroke="#6fbf9f" stroke-width="1"/></svg>Phone : 555-0142-7788</div>
    <div class="row"><svg width="13" height="10" viewBox="0 0 13 10"><rect x=".5" y=".5" width="12" height="9" fill="none" stroke="#6fbf9f"/><path d="M.5,.5 L6.5,5.5 L12.5,.5" fill="none" stroke="#6fbf9f"/></svg>Email : info@lirava.dk</div>
  </div>

  <div class="abs bottom">©2017 Lirava ., All Rights Reserved.</div>
</footer>

</body>
</html>
```